MEDICAL CLINIC LETTERHEAD

Design is a letterhead for a non-profit medical center. The name of the clinic is VITARIDGE Community Health Center. Although the full name must be included, the community health center part is more of a description and should be less visible - i attached an example of what I mean by that (ATTACHED IMAGE IS AN EXAMPLE OF FONT SIZES NOT A DESIGN IDEA). Please design something modern, cool looking and unique because I can always download free templates.
Phone, email, website and etc will be added later.

Industry/Entity Type

MEDICAL

```html
<!DOCTYPE html>
<html lang="en">
<head>
<meta charset="utf-8">
<title>VITARIDGE Community Health Center – Letterhead</title>
<link rel="stylesheet" href="https://fonts.googleapis.com/css2?family=Lato:wght@400;700&family=Mulish:wght@400&family=Italianno&display=swap">
<style>
  :root {
    --navy: #1b2a4a;
    --gold: #b0915c;
    --ink: #2e2e2e;
    --paper: #f9f9fa;
    --backdrop: #d9d9db;
  }
  * { margin: 0; padding: 0; box-sizing: border-box; }
  html, body { width: 1200px; height: 985px; overflow: hidden; }
  body {
    background: var(--backdrop);
    font-family: "Lato", sans-serif;
    color: var(--ink);
  }
  .letterhead {
    position: absolute;
    left: 253px; top: 0;
    width: 694px; height: 985px;
    background: radial-gradient(ellipse at 50% 30%, #ffffff 0%, var(--paper) 60%, #f1f0f2 100%);
    overflow: hidden;
  }
  .brand {
    position: absolute;
    left: 49px; top: 72px;
    display: flex; align-items: center; gap: 10px;
  }
  .brand-mark {
    width: 14px; height: 14px;
    background: var(--gold);
  }
  .brand-name {
    font-family: "Lato", sans-serif;
    font-weight: 700;
    font-size: 34px;
    letter-spacing: 2px;
    color: var(--navy);
  }
  .contact {
    position: absolute;
    left: 475px; top: 40px;
    padding-left: 11px;
    border-left: 1px solid var(--gold);
    font-family: "Mulish", sans-serif;
    font-size: 12px;
    line-height: 16.5px;
    color: #111;
  }
  .contact-name { margin-bottom: 3px; }
  .contact-row { display: flex; align-items: center; gap: 9px; }
  .contact-row svg { width: 12px; height: 10px; flex: none; }
  .letter {
    position: absolute;
    left: 53px; top: 296px;
    width: 587px;
    font-size: 12.6px;
    line-height: 15px;
  }
  .date { margin-bottom: 17px; font-size: 13.5px; }
  .recipient { margin-bottom: 15px; font-size: 13px; line-height: 16px; }
  .address { margin-bottom: 18px; font-size: 13px; line-height: 16px; }
  .salutation { font-weight: 700; font-size: 16px; margin-bottom: 17px; }
  .body-text p { text-align: justify; margin-bottom: 15px; }
  .closing { margin-top: 30px; font-size: 13px; }
  .signature {
    font-family: "Italianno", cursive;
    font-size: 40px;
    color: #333;
    margin-top: 8px;
    line-height: 44px;
  }
  .footer-bands {
    position: absolute;
    left: 0; bottom: 0;
    width: 694px; height: 46px;
    display: block;
  }
</style>
</head>
<body>
  <main class="letterhead">
    <header>
      <div class="brand">
        <span class="brand-mark"></span>
        <span class="brand-name">VITARIDGE</span>
      </div>
      <address class="contact" style="font-style:normal">
        <div class="contact-name">VITARIDGE Community<br>Health Center.</div>
        <div class="contact-row">
          <svg viewBox="0 0 12 10"><path d="M1 3 Q6 0 11 3 L10 5 L8 4 L8 3 Q6 2 4 3 L4 4 L2 5 Z M3 5 L9 5 L10 9 L2 9 Z" fill="var(--gold)"/></svg>
          <span>555-214-3088</span>
        </div>
        <div class="contact-row">
          <svg viewBox="0 0 12 10"><rect x="0.5" y="1" width="11" height="8" fill="var(--gold)"/><path d="M0.5 1 L6 5.5 L11.5 1" fill="none" stroke="#fff" stroke-width="1"/></svg>
          <span>hello@vitaridge-mail.org</span>
        </div>
        <div class="contact-row">
          <svg viewBox="0 0 12 10"><rect x="0.5" y="1" width="11" height="8" fill="var(--gold)"/><path d="M0.5 1 L6 5.5 L11.5 1" fill="none" stroke="#fff" stroke-width="1"/></svg>
          <span>care@vitaridge-web.org</span>
        </div>
      </address>
    </header>

    <section class="letter">
      <p class="date">Feb-03-2022</p>
      <p class="recipient">Mr, Alan Ward<br>President</p>
      <p class="address">Northbay Works<br>123 Street Name, Suite# 10<br>City, State, 120023</p>
      <p class="salutation">Dear Mr, Alan</p>
      <div class="body-text">
        <p>Lorem ipsum dolor sit amet, consectetur adipisicing elit, sed do eiusmod tempor incididunt ut labore et dolore magna aliqua. Ut enim ad minim veniam, quis nostrud exercitation ullamco laboris nisi ut aliquip ex ea commodo consequat. Duis aute irure dolor in reprehenderit in voluptate velit esse cillum dolore eu fugiat nulla pariatur.</p>
        <p>Lorem ipsum dolor sit amet, consectetur adipisicing elit, sed do eiusmod tempor incididunt ut labore et dolore magna aliqua. Ut enim ad minim veniam, quis nostrud exercitation ullamco laboris nisi ut aliquip ex ea commodo consequat. Duis aute irure dolor in reprehenderit in voluptate velit esse cillum dolore eu fugiat nulla pariatur.</p>
        <p>Lorem ipsum dolor sit amet, consectetur adipisicing elit, sed do eiusmod tempor incididunt ut labore et dolore magna aliqua. Ut enim ad minim veniam, quis nostrud exercitation ullamco laboris nisi ut aliquip ex ea commodo consequat.</p>
        <p>Excepteur sint occaecat cupidatat non proident, sunt in culpa qui officia deserunt mollit anim id est laborum. re et dolore magnam aliquam quaerat voluptatem.</p>
      </div>
      <p class="closing">Regards</p>
      <p class="signature">Daniel Reyes</p>
    </section>

    <svg class="footer-bands" viewBox="0 0 694 46" aria-hidden="true">
      <rect x="0" y="6" width="149" height="10" fill="var(--gold)"/>
      <rect x="154" y="6" width="119" height="10" fill="var(--navy)"/>
      <polygon points="278,6 459,6 449,16 278,16" fill="var(--gold)"/>
      <polygon points="0,21 445,21 467,0 694,0 694,46 0,46" fill="var(--navy)"/>
    </svg>
  </main>
</body>
</html>
```